Online business manager needs a website

I need a website designed and then coded. I am an online business manager serving a number of different industries providing administrative support to existing small businesses and helping solo practitioners get their new business up and running.

I didn't have a logo formally designed but have been using the attached avatar and wouldn't mind something that incorporated that.

The business doesn't have an official name, so I've just been using my name Lena Morvath, Online Business Manager or Lena Morvath, OBM. I've attached two documents that I have made previously for an example of content.

I would prefer the final site be in Wordpress.

Requirements
Must have
• A way to contact me, testimonials, list of services

```html
<!DOCTYPE html>
<html lang="en">
<head>
<meta charset="utf-8">
<title>Lena Morvath – Online Business Manager</title>
<link href="https://fonts.googleapis.com/css2?family=Outfit:wght@200;300;400;500;600;700;800&display=swap" rel="stylesheet">
<style>
:root{
  --night:#05062a;
  --night-2:#0b1a5c;
  --blue:#3b5fd6;
  --teal:#2fd3cf;
  --ink:#15161c;
  --body:#2a2b33;
  --mist:#f1f2f4;
  --white:#ffffff;
  --dot:#b9c3e8;
}
*{box-sizing:border-box;margin:0;padding:0}
html,body{width:1200px;height:2616px;overflow:hidden;background:var(--white)}
body{font-family:"Outfit",sans-serif;color:var(--body)}
.canvas{position:relative;width:1200px;height:2616px;overflow:hidden}
.abs{position:absolute}
.bg-svg{position:absolute;left:0;width:1200px}

/* header */
.brand-avatar{left:157px;top:16px;width:58px;height:48px;border-radius:6px;background:linear-gradient(135deg,#f2c77a,#7fb6c9)}
.brand-name{left:222px;top:18px;font-size:20px;font-weight:700;letter-spacing:1.5px;color:var(--teal);line-height:22px}
.brand-role{left:222px;top:42px;font-size:13px;color:var(--white)}
.nav{top:31px;font-size:13px;color:var(--white)}
.nav.active{color:var(--teal)}
.nav-cta{left:918px;top:22px;width:121px;height:36px;border:1.5px solid var(--teal);border-radius:18px;color:var(--white);font-size:13px;text-align:center;line-height:33px}

/* hero */
.hero-first{left:156px;top:148px;font-size:80px;font-weight:200;color:var(--white);line-height:80px;letter-spacing:-1px}
.hero-last{left:156px;top:226px;font-size:76px;font-weight:700;color:var(--white);line-height:80px;letter-spacing:-1px}
.hero-badge{left:160px;top:327px;width:315px;height:34px;background:linear-gradient(90deg,var(--blue),var(--teal));color:var(--white);font-size:15px;letter-spacing:3px;text-align:center;line-height:34px}
.hero-text{left:160px;top:380px;width:385px;font-size:13.5px;line-height:24px;color:var(--white)}
.hero-photo{left:638px;top:117px;width:390px;height:390px;border-radius:50%;background:linear-gradient(160deg,#8a7c6f,#d6a57c 55%,#7d8590)}

/* about */
.about-photo{left:162px;top:657px;width:374px;height:386px;border-radius:187px 187px 0 0;background:linear-gradient(160deg,#c93a8c,#e6b99c 50%,#26222a)}
.h2{font-size:36px;font-weight:300;color:var(--ink);line-height:40px}
.h2 b{font-weight:700}
.about-title{left:610px;top:660px}
.about-sub{left:612px;top:708px;font-size:13px;letter-spacing:3px;color:var(--ink)}
.about-text{left:612px;top:736px;width:425px;font-size:13.5px;line-height:25.5px;color:var(--ink)}
.btn-solid{left:612px;top:990px;width:135px;height:38px;border-radius:19px;background:linear-gradient(90deg,var(--blue),var(--teal));color:var(--white);font-size:13px;font-weight:500;text-align:center;line-height:38px}

/* services */
.services-title{left:0;width:1200px;top:1184px;text-align:center}
.service{width:230px;text-align:center}
.icon-box{position:absolute;width:92px;height:92px}
.icon-box .back1{position:absolute;left:-6px;top:-6px;width:40px;height:40px;border:4px solid var(--blue);border-radius:8px}
.icon-box .back2{position:absolute;right:-6px;bottom:-6px;width:40px;height:40px;border:4px solid var(--teal);border-radius:8px}
.icon-box .face{position:absolute;inset:0;background:var(--white);border-radius:8px;box-shadow:0 6px 18px rgba(20,30,80,.08);display:flex;align-items:center;justify-content:center}
.icon-box.filled .face{background:linear-gradient(135deg,var(--blue),var(--teal))}
.icon-box.filled .back1,.icon-box.filled .back2{border-width:2px;border-color:#9fb0ea}
.service-name{font-size:14.5px;font-weight:600;color:var(--ink);line-height:21px}
.service-list{list-style:none;font-size:13px;line-height:25.5px;color:var(--ink);margin-top:6px}
.btn-outline{left:532px;top:1575px;width:136px;height:38px;border:1.5px solid var(--blue);border-radius:19px;color:var(--blue);font-size:13px;font-weight:500;text-align:center;line-height:35px}

/* testimonials */
.love-title{left:0;width:1200px;top:1757px;text-align:center}
.client-photo{left:244px;top:1834px;width:174px;height:174px;border-radius:50%;background:linear-gradient(150deg,#6b8a4a,#b66a5a 55%,#2b2a3a)}
.client-ring{left:238px;top:1828px;width:186px;height:186px;border-radius:50%;border:1.5px solid var(--blue)}
.quote-text{left:458px;top:1862px;width:490px;font-size:13.5px;line-height:25.5px;color:var(--ink)}
.quote-name{left:458px;top:1977px;font-size:13px;font-weight:600;letter-spacing:1.5px;color:var(--ink)}
.quote-company{left:458px;top:2001px;font-size:13px;color:var(--ink)}
.arrow{width:36px;height:36px;border-radius:50%}

/* connect */
.connect-title{left:0;width:1200px;top:2203px;text-align:center;color:var(--white)}
.contact{width:206px;text-align:center;color:var(--white)}
.contact-label{font-size:13px;letter-spacing:1px}
.contact-value{font-size:14px;font-weight:600;margin-top:8px}
.rule{left:160px;top:2553px;width:880px;height:1px;background:rgba(255,255,255,.15)}
.copy{left:0;width:1200px;top:2582px;text-align:center;font-size:13px;color:var(--white)}
</style>
</head>
<body>
<div class="canvas">

  <svg class="bg-svg" style="top:0" height="580" viewBox="0 0 1200 580" aria-hidden="true">
    <defs>
      <linearGradient id="heroGrad" x1="0" y1="0" x2="0" y2="1">
        <stop offset="0" stop-color="#04051f"/>
        <stop offset="0.7" stop-color="#070c3d"/>
        <stop offset="1" stop-color="#0e2a7a"/>
      </linearGradient>
    </defs>
    <path d="M0 0H1200V505Q600 650 0 505Z" fill="url(#heroGrad)"/>
    <circle cx="117" cy="129" r="2" fill="#3d6cff"/>
    <circle cx="580" cy="465" r="1.5" fill="#6e8cff"/>
    <circle cx="1130" cy="360" r="1" fill="#8aa2ff"/>
    <circle cx="334" cy="525" r="1" fill="#8aa2ff"/>
    <circle cx="834" cy="313" r="205" fill="none" stroke="var(--blue)" stroke-width="1.5"/>
    <circle cx="838" cy="309" r="204" fill="none" stroke="var(--teal)" stroke-width="1.5"/>
  </svg>

  <div class="abs brand-avatar" role="img" aria-label="Illustrated avatar of the business manager at a laptop"></div>
  <div class="abs brand-name">LENA MORVATH</div>
  <div class="abs brand-role">Online Business Manager</div>
  <div class="abs nav active" style="left:543px">Home</div>
  <div class="abs nav" style="left:610px">About Me</div>
  <div class="abs nav" style="left:700px">What I Do Best</div>
  <div class="abs nav" style="left:822px">Client Love</div>
  <div class="abs nav-cta">Contact Me</div>

  <div class="abs hero-first">LENA</div>
  <div class="abs hero-last">MORVATH</div>
  <div class="abs hero-badge">DIGITAL BUSINESS MANAGER</div>
  <p class="abs hero-text">Focused on the live event and entertainment industry. Helping artists and owners to better manage their career and business by strategically reviewing systems, recommending operational efficiencies, and managing inboxes.</p>
  <div class="abs hero-photo" role="img" aria-label="Portrait photo of Lena Morvath outdoors in a city street"></div>

  <div class="abs about-photo" role="img" aria-label="Photo of Lena Morvath in front of pink flowering shrubs"></div>
  <h2 class="abs h2 about-title">About <b>Me</b></h2>
  <div class="abs about-sub">LENA MORVATH, VIRTUAL ASSISTANT</div>
  <p class="abs about-text">Hi! I'm so excited that you have chosen to explore my portfolio. Helping businesses achieve their goals is my passion, and I'm thrilled that with my assistance you will have more time for your own passion project. I thrive while working independently, which means you can be confident when leaving tasks for me. The type of work that lights me up is anything involving organization and/or spreadsheets. You need data analyzed that includes multiple nested if formulas? You have an overwhelming amount of email to sort through and appointments to book? I'm your gal!</p>
  <div class="abs btn-solid">Contact Me</div>

  <svg class="bg-svg" style="top:1115px" height="660" viewBox="0 0 1200 660" aria-hidden="true">
    <path d="M0 80Q600 -80 1200 80V648Q600 560 0 648Z" fill="var(--mist)"/>
    <path d="M160 305Q420 150 600 165T1040 305" fill="none" stroke="#9aa0aa" stroke-width="1.2" stroke-dasharray="3 4"/>
  </svg>
  <h2 class="abs h2 services-title">What I <b>Do Best</b></h2>

  <div class="abs icon-box" style="left:216px;top:1312px"><span class="back1"></span><span class="back2"></span><span class="face">
    <svg width="52" height="52" viewBox="0 0 52 52" fill="none" stroke="var(--blue)" stroke-width="1.8"><path d="M8 30V24a18 18 0 0 1 36 0v6"/><rect x="5" y="28" width="7" height="13" rx="3"/><rect x="40" y="28" width="7" height="13" rx="3"/><circle cx="26" cy="26" r="12" stroke="var(--teal)"/><path d="M21 24v4M24 22v8M27 21v10M30 23v6"/></svg>
  </span></div>
  <div class="abs icon-box filled" style="left:442px;top:1260px"><span class="back1"></span><span class="back2"></span><span class="face">
    <svg width="52" height="52" viewBox="0 0 52 52" fill="none" stroke="#fff" stroke-width="1.8"><rect x="4" y="6" width="20" height="16" rx="2"/><path d="M6 20l6-7 5 5 3-3 4 5"/><rect x="28" y="6" width="20" height="16" rx="2"/><path d="M31 11h14M31 15h14M31 19h8"/><path d="M5 30h18v10H12l-5 4v-4H5z"/><rect x="28" y="28" width="20" height="16" rx="2"/><path d="M35 32l7 4-7 4z"/></svg>
  </span></div>
  <div class="abs icon-box" style="left:667px;top:1260px"><span class="back1"></span><span class="back2"></span><span class="face">
    <svg width="52" height="52" viewBox="0 0 52 52" fill="none" stroke="var(--blue)" stroke-width="1.8"><rect x="4" y="20" width="32" height="26" rx="2"/><path d="M10 40v-6M16 40v-10M22 40v-8M28 40v-14" stroke="var(--teal)"/><path d="M8 16l8-6 8 4 8-8"/><circle cx="40" cy="14" r="9"/><path d="M40 5v9h9"/></svg>
  </span></div>
  <div class="abs icon-box" style="left:893px;top:1312px"><span class="back1"></span><span class="back2"></span><span class="face">
    <svg width="52" height="52" viewBox="0 0 52 52" fill="none" stroke="var(--blue)" stroke-width="1.8"><circle cx="26" cy="26" r="18" stroke-dasharray="7 4"/><circle cx="26" cy="26" r="12"/><circle cx="26" cy="22" r="4" stroke="var(--teal)"/><path d="M18 34c2-5 14-5 16 0" stroke="var(--teal)"/></svg>
  </span></div>

  <div class="abs service" style="left:147px;top:1424px">
    <div class="service-name">Virtual Assistance</div>
    <ul class="service-list"><li>Calendar Management</li><li>Email Management</li><li>Light Graphic Design</li><li>Data Entry</li></ul>
  </div>
  <div class="abs service" style="left:373px;top:1372px">
    <div class="service-name">Social Media &amp;<br>Content Management</div>
    <ul class="service-list"><li>Content Repurposing</li><li>Graphics Creation</li><li>Audiogram Creation</li><li>Search Engine Optimization</li></ul>
  </div>
  <div class="abs service" style="left:598px;top:1372px">
    <div class="service-name">Finance Management</div>
    <ul class="service-list"><li>Create Invoices</li><li>Track Receivables</li><li>Analyze Expenses</li><li>Year Over Year Analytics</li></ul>
  </div>
  <div class="abs service" style="left:823px;top:1424px">
    <div class="service-name">Business Management</div>
    <ul class="service-list"><li>Creation of Operating Procedures</li><li>Review of Website Strategy</li><li>Reporting and Analytics</li><li>Project Management</li></ul>
  </div>
  <div class="abs btn-outline">Contact Me</div>

  <h2 class="abs h2 love-title">Client <b>Love</b></h2>
  <svg class="abs arrow" style="left:161px;top:1903px" viewBox="0 0 36 36" aria-hidden="true"><circle cx="18" cy="18" r="17" fill="#fff" stroke="#d6d8de"/><path d="M24 18H12M17 13l-5 5 5 5" fill="none" stroke="#9aa0aa" stroke-width="1.5"/></svg>
  <svg class="abs arrow" style="left:1003px;top:1903px" viewBox="0 0 36 36" aria-hidden="true"><circle cx="18" cy="18" r="17" fill="#fff" stroke="var(--teal)"/><path d="M12 18h12M19 13l5 5-5 5" fill="none" stroke="var(--blue)" stroke-width="1.5"/></svg>
  <div class="abs client-ring"></div>
  <div class="abs client-photo" role="img" aria-label="Photo of client Dana R. outdoors"></div>
  <svg class="abs" style="left:458px;top:1825px" width="34" height="24" viewBox="0 0 34 24" aria-hidden="true"><defs><linearGradient id="qg" x1="0" x2="1"><stop offset="0" stop-color="var(--blue)"/><stop offset="1" stop-color="var(--teal)"/></linearGradient></defs><path d="M14 6C8 6 3 9 3 16a7 7 0 0 0 14 0 7 7 0 0 0-8-7c1-2 3-3 5-3zM31 6c-6 0-11 3-11 10a7 7 0 0 0 14 0 7 7 0 0 0-8-7c1-2 3-3 5-3z" fill="url(#qg)"/></svg>
  <p class="abs quote-text">When it became apparent that a project would take more time than I had, Lena stepped up to take on the required research. She was thorough and timely; able to meet a last-minute 12-hour deadline. I would highly recommend Lena to assist with your next project.</p>
  <div class="abs quote-name">- DANA R. OWNER</div>
  <div class="abs quote-company">Northgate Roofing Co.</div>
  <svg class="abs" style="left:563px;top:2052px" width="74" height="12" viewBox="0 0 74 12" aria-hidden="true"><circle cx="6" cy="6" r="3" fill="var(--dot)"/><circle cx="26" cy="6" r="4" fill="none" stroke="var(--blue)" stroke-width="2"/><circle cx="46" cy="6" r="3" fill="var(--dot)"/><circle cx="66" cy="6" r="3" fill="var(--dot)"/></svg>

  <svg class="bg-svg" style="top:2130px" height="486" viewBox="0 0 1200 486" aria-hidden="true">
    <defs>
      <linearGradient id="footGrad" x1="0" y1="0" x2="0" y2="1">
        <stop offset="0" stop-color="#04051f"/>
        <stop offset="0.6" stop-color="#07093a"/>
        <stop offset="1" stop-color="#0c1f6e"/>
      </linearGradient>
    </defs>
    <path d="M0 83Q600 -83 1200 83V486H0Z" fill="url(#footGrad)"/>
    <circle cx="122" cy="124" r="2" fill="#3d6cff"/>
    <circle cx="1028" cy="303" r="3" fill="#3d6cff"/>
    <g fill="none" stroke-width="1.3">
      <circle cx="267" cy="248" r="103" stroke="var(--teal)"/><circle cx="263" cy="251" r="102" stroke="var(--blue)"/>
      <circle cx="489" cy="248" r="103" stroke="var(--teal)"/><circle cx="485" cy="251" r="102" stroke="var(--blue)"/>
      <circle cx="711" cy="248" r="103" stroke="var(--teal)"/><circle cx="707" cy="251" r="102" stroke="var(--blue)"/>
      <circle cx="933" cy="248" r="103" stroke="var(--teal)"/><circle cx="929" cy="251" r="102" stroke="var(--blue)"/>
    </g>
    <g fill="none" stroke="var(--blue)" stroke-width="2">
      <path d="M253 213c-3 2-4 6-1 11l8 10c4 4 8 5 11 3l3-3-6-6-3 2-8-9 2-3-6-6z"/>
      <rect x="265" y="208" width="16" height="11" rx="2" stroke="var(--teal)"/>
      <path d="M470 220h38v22h-38zM470 220l19 13 19-13"/><path d="M477 218v-10h24v10M481 213h16" stroke="var(--teal)"/>
      <rect x="693" y="204" width="36" height="36" rx="6"/><circle cx="711" cy="222" r="8" stroke="var(--teal)"/>
      <rect x="915" y="204" width="36" height="36" rx="6"/><rect x="923" y="212" width="20" height="20" rx="3" stroke="var(--teal)"/>
    </g>
  </svg>
  <h2 class="abs h2 connect-title">Let's <b>Connect</b></h2>
  <div class="abs contact" style="left:164px;top:2385px"><div class="contact-label">PHONE</div><div class="contact-value">555.318.2046</div></div>
  <div class="abs contact" style="left:386px;top:2385px"><div class="contact-label">EMAIL</div><div class="contact-value" style="font-size:12px">lenamorvath.obm@mailbox.net</div></div>
  <div class="abs contact" style="left:608px;top:2385px"><div class="contact-label">NETWORK</div><div class="contact-value">Lena Ivy Morvath</div></div>
  <div class="abs contact" style="left:830px;top:2385px"><div class="contact-label">SOCIAL</div><div class="contact-value">/LenaIvy12</div></div>
  <div class="abs rule"></div>
  <div class="abs copy">© 2023 Lena Morvath. All Rights Reserved.</div>

</div>
</body>
</html>
```